Local fast-growing company in the service sector

We are looking for a modern business card design, which should also appear on our letterheads

Target Market(s)

Private and industrial sectors

Contact Information for Business Card

Vorname Name
Kellberger Str. 18
73614 Lindenfeld
Tel.: 07146-839214-0
Name@agentur-kvtl.de

Colors
9d9d9d
919191
aaaaaa

Requirements
Must have
• The logo (file) in silver

```html
<!DOCTYPE html>
<html lang="de">
<head>
<meta charset="utf-8">
<title>KVTL – Visitenkarte</title>
<link rel="stylesheet" href="https://fonts.googleapis.com/css2?family=Michroma&family=Montserrat:wght@400;500&display=swap">
<style>
  :root{
    --backdrop:#4a4a4a;
    --card:#2a2a2b;
    --card-edge:#333334;
    --silver:#aaaaaa;
    --silver-mid:#9d9d9d;
    --silver-dark:#919191;
    --text-light:#e6e6e6;
  }
  *{margin:0;padding:0;box-sizing:border-box}
  html,body{width:799px;height:1200px;overflow:hidden}
  body{
    background:var(--backdrop);
    display:flex;flex-direction:column;align-items:center;justify-content:space-around;
    padding:60px 0;
  }
  .card{
    position:relative;
    width:620px;height:360px;
    background:radial-gradient(ellipse at 55% 40%, var(--card-edge), var(--card) 75%);
    box-shadow:0 18px 40px rgba(0,0,0,.45);
  }
  .brand{
    display:flex;align-items:center;gap:18px;
  }
  .brand-mark{
    width:58px;height:58px;background:var(--silver);
  }
  .brand-name{
    font-family:"Michroma",sans-serif;
    font-size:64px;line-height:1;letter-spacing:2px;
    color:var(--silver);
  }
  .card-front .brand{
    position:absolute;left:50%;top:50%;transform:translate(-50%,-50%);
  }
  .holder-name{
    position:absolute;left:48px;top:52px;
    font-family:"Michroma",sans-serif;font-weight:400;
    font-size:22px;letter-spacing:3px;
    color:var(--silver-dark);
  }
  .contact{
    position:absolute;left:48px;bottom:58px;
    font-family:"Montserrat",sans-serif;font-size:15px;line-height:1.5;
    color:var(--text-light);list-style:none;
  }
  .contact li{display:flex;align-items:center;gap:10px}
  .contact svg{width:13px;height:13px;fill:none;stroke:var(--text-light);stroke-width:1.6}
  .card-back .brand{
    position:absolute;right:48px;bottom:52px;gap:14px;
  }
  .card-back .brand-mark{width:44px;height:44px}
  .card-back .brand-name{font-size:48px}
</style>
</head>
<body>
  <section class="card card-front">
    <div class="brand">
      <span class="brand-mark"></span>
      <span class="brand-name">KVTL</span>
    </div>
  </section>

  <section class="card card-back">
    <h1 class="holder-name">VORNAME NAME</h1>
    <ul class="contact">
      <li class="address">Kellberger Str. 18</li>
      <li class="address">73614 Lindenfeld</li>
      <li>
        <svg viewBox="0 0 16 16"><path d="M4 1.5h2.5l1 3.5-1.8 1.2a8 8 0 0 0 4.1 4.1l1.2-1.8 3.5 1V12a2.5 2.5 0 0 1-2.5 2.5A11 11 0 0 1 1.5 4 2.5 2.5 0 0 1 4 1.5z"/></svg>
        07146-839214-0
      </li>
      <li>
        <svg viewBox="0 0 16 16"><rect x="1.5" y="3.5" width="13" height="9"/><path d="M1.5 3.5 8 9l6.5-5.5"/></svg>
        Name@agentur-kvtl.de
      </li>
      <li>
        <svg viewBox="0 0 16 16"><circle cx="8" cy="8" r="6.5"/><path d="M1.5 8h13M8 1.5c-3 3.5-3 9.5 0 13M8 1.5c3 3.5 3 9.5 0 13"/></svg>
        www.agentur-kvtl.de
      </li>
    </ul>
    <div class="brand">
      <span class="brand-mark"></span>
      <span class="brand-name">KVTL</span>
    </div>
  </section>
</body>
</html>
```